Tidewell Homecare

I am looking to have a website designed for a housekeeping company that looks similar to this one. https://marloweshomecare.example/

I need 5 websites designed but will start with this one to see how I like it.

Industry/Entity Type

House Cleaning

Coding

Coded - Design and coding required

Number of Pages Required

5+ page

Font styles to use
Serif
Script

Colors
ffffff
fdf9cf
fbf289
fbee3f
d6edf3
86cae7
33a6d7
edf1f8
cedeed

```html
<!DOCTYPE html>
<html lang="en">
<head>
<meta charset="utf-8">
<title>Tidewell Homecare</title>
<link href="https://fonts.googleapis.com/css2?family=Playfair+Display:wght@400;700&family=Montserrat:wght@600;700&family=Roboto:wght@400;500;700&display=swap" rel="stylesheet">
<style>
:root{
  --white:#ffffff;
  --blue:#33a6d7;
  --blue-deep:#2a8fc9;
  --sky:#86cae7;
  --ice:#d6edf3;
  --mist:#edf1f8;
  --form:#c4d6e8;
  --field:#cedeed;
  --ink:#1d1d1d;
  --text:#333333;
  --star:#fbee3f;
  --sand:#fdf9cf;
}
*{margin:0;padding:0;box-sizing:border-box}
html,body{width:1200px;height:4071px;overflow:hidden;background:var(--white)}
body{position:relative;font-family:'Roboto',sans-serif;color:var(--text)}
.abs{position:absolute}
.serif{font-family:'Playfair Display',serif}
.center{text-align:center}

/* hero */
.hero{left:0;top:0;width:1200px;height:680px;background:linear-gradient(90deg,#6f7d55 0%,#8b7f6a 20%,#b7b0a6 35%,#cfcac3 60%,#e5e2de 80%,#d8d4cf 100%)}
.brand{left:82px;top:58px;display:flex;align-items:center;gap:10px;font-family:'Roboto',sans-serif;font-weight:700;font-size:26px;color:var(--white)}
.brand-dot{width:18px;height:18px;border-radius:50%;background:var(--blue)}
.nav{right:68px;top:42px;display:flex;gap:36px;font-size:15px;color:var(--white);align-items:center}
.nav .on{font-weight:700}
.hero-kicker{left:0;width:1200px;top:346px;font-family:'Montserrat',sans-serif;font-weight:700;font-size:25px;color:var(--white);letter-spacing:.5px}
.hero-title{left:0;width:1200px;top:378px;font-family:'Playfair Display',serif;font-weight:700;font-size:56px;color:var(--white);letter-spacing:3px}
.btn{background:var(--blue);color:var(--white);font-weight:700;font-size:14px;display:flex;align-items:center;justify-content:center;text-transform:uppercase}
.hero-btn{left:516px;top:455px;width:169px;height:45px;background:var(--blue-deep)}
.dots{left:578px;top:638px;display:flex;gap:14px}
.dots span{width:14px;height:14px;border-radius:50%;border:2px solid var(--white)}
.dots span:first-child{background:var(--white)}

/* welcome */
.welcome-title{left:0;width:1200px;top:736px;font-weight:700;font-size:40px;color:var(--ink)}
.lead{left:250px;width:700px;top:810px;font-size:16px;line-height:22px;color:var(--ink)}
.service-photo{top:937px;width:514px;height:370px}
.service-photo .cap{position:absolute;left:0;right:0;bottom:30px;text-align:center;font-family:'Playfair Display',serif;font-size:40px;color:var(--white)}
.res{left:74px;background:linear-gradient(180deg,#c9ccc6 0%,#9ea39c 55%,#2b2b2b 100%)}
.com{left:613px;background:linear-gradient(180deg,#c46a45 0%,#a8856e 45%,#3a3232 100%)}
.service-text{top:1334px;width:440px;font-size:16px;line-height:22px;color:var(--ink)}
.service-btn{top:1420px;width:214px;height:44px;background:#4aa3d8;font-size:14px}

/* works */
.works{left:0;top:1583px;width:1200px;height:577px;background:linear-gradient(90deg,#2a8fd0,#5eb0dd)}
.works-photo{left:0;top:1583px;width:1200px;height:577px}
.works-title{left:82px;top:1680px;font-size:40px;color:var(--white)}
.works-text{left:82px;top:1752px;width:485px;font-size:14.5px;line-height:22px;color:var(--white)}
.outline-btn{left:82px;top:1922px;width:180px;height:48px;border:2px solid var(--white);color:var(--white);font-weight:700;font-size:18px;display:flex;align-items:center;justify-content:center}

/* form */
.form-box{left:98px;top:2076px;width:1004px;height:329px;background:var(--form)}
.form-title{left:0;width:1200px;top:2106px;font-size:40px;color:var(--ink)}
.field{width:223px;height:48px;border:1px solid #e2ebf4;background:var(--field);font-size:12px;color:#222;padding-left:16px;display:flex;align-items:center}
.submit{left:534px;top:2375px;width:130px;height:44px;font-size:14px}

/* testimonials */
.sec-title{left:0;width:1200px;font-size:40px;color:var(--ink)}
.t-card{top:2571px;width:302px;height:294px;background:var(--white);box-shadow:0 2px 10px rgba(0,0,0,.12)}
.t-card.feature{background:var(--blue)}
.stars{position:absolute;top:46px;left:0;right:0;text-align:center;font-size:16px;letter-spacing:8px;color:var(--star)}
.quote{position:absolute;top:96px;left:30px;right:30px;text-align:center;font-size:13px;line-height:16.5px;color:#444}
.who{position:absolute;top:186px;left:0;right:0;text-align:center;font-family:'Montserrat',sans-serif;font-weight:700;font-size:20px;color:var(--blue)}
.feature .quote,.feature .who{color:var(--white)}
.avatar{top:2800px;width:98px;height:98px;border-radius:50%;border:5px solid var(--blue);background:linear-gradient(135deg,#c98f72,#6b4634)}

/* vendors */
.vendor{top:3083px;width:230px;height:209px;background:var(--white);box-shadow:0 2px 10px rgba(0,0,0,.1);display:flex;align-items:center;justify-content:center;font-weight:700;font-size:22px;color:#222;letter-spacing:1px}

/* newsletter */
.news{left:0;top:3372px;width:1200px;height:422px;background:linear-gradient(180deg,#cfe4f3 0%,#9fd0e6 35%,#3e9fc4 52%,#e9e2d2 70%,#f0e9dc 100%)}
.news-title{left:0;width:1200px;top:3440px;font-size:40px;color:var(--ink)}
.news-sub{left:0;width:1200px;top:3496px;font-size:16px;color:var(--ink)}
.rule{left:568px;top:3537px;width:64px;height:3px;background:#333}
.news-input{left:324px;top:3606px;width:550px;height:78px;background:var(--white);font-size:21px;color:#222;padding-left:28px;display:flex;align-items:center}
.news-btn{left:696px;top:3616px;width:170px;height:58px;font-weight:400;font-size:22px;text-transform:none}

/* footer */
.foot-links{left:81px;top:3870px;font-size:17px;line-height:33px;color:#111}
.social{left:462px;top:3870px;font-size:17px;line-height:33px;color:#111}
.social div{display:flex;align-items:center;gap:20px}
.social i{width:16px;height:16px;border-radius:50%;background:#111;display:inline-block}
.copy{right:76px;top:3896px;font-size:17px;color:#111}
.cards{left:880px;top:3950px;display:flex;gap:12px}
.cards span{width:32px;height:18px;border-radius:3px;background:var(--ice);border:1px solid #c9d3dc}
</style>
</head>
<body>

<div class="abs hero" role="img" aria-label="Photo of a hand opening a white door into a bright living room with a plant and armchair"></div>
<div class="abs brand"><span class="brand-dot"></span>Tidewell Homecare</div>
<nav class="abs nav"><span class="on">HOME</span><span>ABOUT US</span><span>SERVICES</span><span>NEWS</span><span>CONTACT US</span>
<svg width="18" height="18" viewBox="0 0 18 18"><circle cx="7.5" cy="7.5" r="5.5" fill="none" stroke="#fff" stroke-width="2.5"/><line x1="11.5" y1="11.5" x2="16" y2="16" stroke="#fff" stroke-width="2.5"/></svg></nav>
<div class="abs hero-kicker center">TIDEWELL HOMECARE</div>
<div class="abs hero-title center">LORIUM IPSUM</div>
<div class="abs btn hero-btn">Learn More</div>
<svg class="abs" style="left:134px;top:628px" width="24" height="20" viewBox="0 0 24 20"><path d="M22 10H4M11 3L4 10l7 7" stroke="#fff" stroke-width="3" fill="none"/></svg>
<svg class="abs" style="left:1044px;top:628px" width="24" height="20" viewBox="0 0 24 20"><path d="M2 10h18M13 3l7 7-7 7" stroke="#fff" stroke-width="3" fill="none"/></svg>
<div class="abs dots"><span></span><span></span></div>

<h1 class="abs serif center welcome-title">Welcome To Tidewell Homecare</h1>
<p class="abs center lead">Sed ut perspiciatis unde omnis iste natus error sit voluptatem accusantium doloremque laudantium, totam rem aperiam, eaque ipsa quae ab illo inventore veritatis et quasi architecto beatae vitae dicta sunt explicabo. Nemo enim ipsam voluptatem.</p>

<div class="abs service-photo res" role="img" aria-label="Photo of paper towel rolls on a kitchen counter"><div class="cap">Residential Cleaning</div></div>
<div class="abs service-photo com" role="img" aria-label="Photo of a housekeeper making a bed in a hotel room"><div class="cap">Commercial / Office</div></div>
<p class="abs center service-text" style="left:111px">Sed ut perspiciatis unde omnis iste natus error sit voluptatem accusantium doloremque laudantium, totam rem aperiam, eaque ipsa quae ab.</p>
<p class="abs center service-text" style="left:650px">Sed ut perspiciatis unde omnis iste natus error sit voluptatem accusantium doloremque laudantium, totam rem aperiam, eaque ipsa quae ab.</p>
<div class="abs btn service-btn" style="left:224px">Residential Service</div>
<div class="abs btn service-btn" style="left:763px">Commercial Service</div>

<div class="abs works"></div>
<svg class="abs works-photo" viewBox="0 0 1200 577" role="img" aria-label="Photo of a city skyline across the water at sunset">
<defs><linearGradient id="dusk" x1="0" y1="0" x2="0" y2="1"><stop offset="0" stop-color="#5f84a3"/><stop offset=".45" stop-color="#c9b08a"/><stop offset=".62" stop-color="#e3a040"/><stop offset="1" stop-color="#6b5130"/></linearGradient></defs>
<polygon points="669,0 1200,0 1200,577 601,577" fill="url(#dusk)"/></svg>
<h2 class="abs serif works-title">Our Works</h2>
<p class="abs works-text">Sed ut perspiciatis unde omnis iste natus error sit voluptatem accusantium doloremque laudantium, totam rem aperiam, eaque ipsa quae ab illo inventore veritatis et quasi architecto beatae vitae dicta sunt explicabo. Nemo enim ipsam voluptatem quia voluptas sit aspernatur aut odit aut fugit, sed quia consequuntur magni dolores eos qui ratione voluptatem sequi nesciunt. Neque porro quisquam est, qui dolorem</p>
<div class="abs outline-btn">GET IN TOUCH</div>

<div class="abs form-box"></div>
<h2 class="abs serif center form-title">Free Estimation / Contact Us</h2>
<div class="abs field" style="left:128px;top:2201px">Name*</div>
<div class="abs field" style="left:368px;top:2201px">Email*</div>
<div class="abs field" style="left:609px;top:2201px">City*</div>
<div class="abs field" style="left:849px;top:2201px">Square Footage*</div>
<div class="abs field" style="left:128px;top:2273px">Property Type*</div>
<div class="abs field" style="left:368px;top:2273px">Type Of Cleaning*</div>
<div class="abs field" style="left:609px;top:2273px">Frequency*</div>
<div class="abs field" style="left:849px;top:2273px;justify-content:space-between;padding-right:16px">mm/dd/yyyy
<svg width="12" height="12" viewBox="0 0 12 12"><rect x="1" y="2" width="10" height="9" fill="none" stroke="#33a6d7" stroke-width="1.5"/><line x1="1" y1="5" x2="11" y2="5" stroke="#33a6d7" stroke-width="1.5"/></svg></div>
<div class="abs btn submit">Submit</div>

<h2 class="abs serif center sec-title" style="top:2484px">Testimonials</h2>
<div class="abs t-card" style="left:117px"><div class="stars">★★★★☆</div><p class="quote">Nor again is there anyone who loves or pursues or desires to obtain pain of itself, because it is pain, but because occasionally circumstances</p><div class="who">Amanda</div></div>
<div class="abs t-card feature" style="left:447px"><div class="stars">★★★★☆</div><p class="quote">Nor again is there anyone who loves or pursues or desires to obtain pain of itself, because it is pain, but because occasionally circumstances</p><div class="who">Smith</div></div>
<div class="abs t-card" style="left:781px"><div class="stars">★★★★☆</div><p class="quote">Nor again is there anyone who loves or pursues or desires to obtain pain of itself, because it is pain, but because occasionally circumstances</p><div class="who">Stephen</div></div>
<div class="abs avatar" style="left:219px" role="img" aria-label="Portrait photo of Amanda"></div>
<div class="abs avatar" style="left:549px" role="img" aria-label="Portrait photo of Smith"></div>
<div class="abs avatar" style="left:883px" role="img" aria-label="Portrait photo of Stephen"></div>

<h2 class="abs serif center sec-title" style="top:2988px">Preferred Vendors</h2>
<div class="abs vendor" style="left:74px">NORTHWIND</div>
<div class="abs vendor" style="left:348px">BRIGHTVALE</div>
<div class="abs vendor" style="left:621px">HARBORLINE</div>
<div class="abs vendor" style="left:895px">SALTMERE</div>

<div class="abs news" role="img" aria-label="Photo of a beach with a wicker picnic basket and towel on the sand"></div>
<h2 class="abs serif center news-title">Subscribe to our newsletter</h2>
<p class="abs center news-sub">Sign up for our email list and get 15% off your first order</p>
<div class="abs rule"></div>
<div class="abs news-input">Your email</div>
<div class="abs btn news-btn">Subscribe</div>

<div class="abs foot-links"><div>Return Policy</div><div>Search</div><div>Blog</div><div>Contact us</div><div>About us</div></div>
<div class="abs social"><div><i></i>Circlepage</div><div><i></i>Chirpline</div><div><i></i>Photoloop</div></div>
<div class="abs copy">© 2020, www.tidewellhomecare.example</div>
<div class="abs cards"><span></span><span></span><span></span><span></span><span></span><span></span></div>

</body>
</html>
```